Professional Photography Business cards

I need business cards that include my logo which I have uploaded. I run a photography business. I am open to ideas but I would like one side to have my logo and the other side to have my contact info. I don't have a website made but I do own a website domain. I have uploaded 2 different logo color schemes. My business colors are Blue, black , and white.

Business Name
Business Phone Number
Business Email
Business Website address
Instagram

Industry/Entity Type

Professional Photography

Contact Information for Business Card

Phone Number: 916-384-7702 email: info@tlane-studio.example Instagram: @t.lanestudio website doman- www.tlane-studio.example

Requirements
Must have
• I like the idea of a business card with a full black background front and back of card. My colors must include royal blue, black, and white

```html
<!DOCTYPE html>
<html lang="en">
<head>
<meta charset="utf-8">
<title>T. Lane Studio – Business Cards</title>
<link rel="stylesheet" href="https://fonts.googleapis.com/css2?family=Arimo:wght@400;700&display=swap">
<style>
  :root {
    --stage: #1e1e1e;
    --card: #151515;
    --card-edge: #0d0d0d;
    --royal-blue: #3039a8;
    --white: #f4f4f4;
    --gloss: #3a3a3a;
  }
  * { box-sizing: border-box; margin: 0; padding: 0; }
  html, body {
    width: 1200px;
    height: 900px;
    overflow: hidden;
    background: var(--stage);
    font-family: "Arimo", Arial, sans-serif;
  }
  .stage {
    position: relative;
    width: 1200px;
    height: 900px;
  }
  .card {
    position: absolute;
    left: 250px;
    width: 700px;
    height: 400px;
    background: var(--card);
    border: 1px solid var(--card-edge);
    box-shadow: 0 10px 30px rgba(0,0,0,0.55);
    overflow: hidden;
  }
  .card--front { top: 34px; }
  .card--back { top: 466px; }

  /* Front: tone-on-tone brand name */
  .front-brand {
    position: absolute;
    inset: 0;
    display: flex;
    align-items: center;
    justify-content: center;
    gap: 18px;
  }
  .front-brand__name {
    font-size: 52px;
    font-weight: 700;
    letter-spacing: 2px;
    color: var(--gloss);
  }
  .front-brand__dot {
    width: 46px;
    height: 46px;
    border-radius: 50%;
    background: var(--gloss);
  }

  /* Back: contact side */
  .back-brand {
    position: absolute;
    left: 40px;
    top: 150px;
    width: 250px;
    display: flex;
    align-items: center;
    gap: 12px;
  }
  .back-brand__name {
    font-size: 30px;
    font-weight: 700;
    color: var(--white);
    line-height: 1.1;
  }
  .back-brand__dot {
    flex: none;
    width: 34px;
    height: 34px;
    border-radius: 50%;
    background: var(--royal-blue);
  }
  .divider {
    position: absolute;
    left: 320px;
    top: 95px;
    width: 2px;
    height: 190px;
    background: var(--royal-blue);
  }
  .contact {
    position: absolute;
    left: 350px;
    top: 100px;
    color: var(--white);
  }
  .contact__name {
    font-size: 30px;
    font-weight: 700;
    color: var(--royal-blue);
    line-height: 1;
  }
  .contact__title {
    font-size: 17px;
    margin-top: 4px;
    margin-bottom: 18px;
  }
  .contact__list { list-style: none; }
  .contact__item {
    display: flex;
    align-items: center;
    gap: 10px;
    font-size: 17px;
    line-height: 1;
    margin-bottom: 10px;
  }
  .contact__icon {
    flex: none;
    width: 14px;
    height: 14px;
    fill: var(--royal-blue);
    stroke: var(--royal-blue);
  }
  .contact__marker {
    flex: none;
    width: 12px;
    height: 12px;
    margin: 0 1px;
    border-radius: 50%;
    background: var(--royal-blue);
  }
  .accent-band {
    position: absolute;
    left: 0;
    right: 0;
    bottom: 0;
    height: 12px;
    background: var(--royal-blue);
  }
</style>
</head>
<body>
<main class="stage">

  <section class="card card--front" aria-label="Card front">
    <div class="front-brand">
      <span class="front-brand__dot"></span>
      <span class="front-brand__name">T. Lane Studio</span>
    </div>
  </section>

  <section class="card card--back" aria-label="Card back">
    <div class="back-brand">
      <span class="back-brand__dot"></span>
      <span class="back-brand__name">T. Lane Studio</span>
    </div>

    <div class="divider"></div>

    <div class="contact">
      <p class="contact__name">Dana Whitfield</p>
      <p class="contact__title">Managing Director</p>
      <ul class="contact__list">
        <li class="contact__item">
          <svg class="contact__icon" viewBox="0 0 24 24" stroke-width="0"><path d="M6.6 10.8a15.1 15.1 0 0 0 6.6 6.6l2.2-2.2c.3-.3.7-.4 1-.2 1.1.4 2.3.6 3.6.6.6 0 1 .4 1 1V20c0 .6-.4 1-1 1A17 17 0 0 1 3 4c0-.6.4-1 1-1h3.5c.6 0 1 .4 1 1 0 1.3.2 2.5.6 3.6.1.3 0 .7-.2 1z"/></svg>
          <span>916-384-7702</span>
        </li>
        <li class="contact__item">
          <svg class="contact__icon" viewBox="0 0 24 24" stroke-width="0"><path d="M2 5h20v14H2z M3.5 6.5 12 13l8.5-6.5" /><path d="M3 6l9 7 9-7" fill="none" stroke="#151515" stroke-width="1.6"/></svg>
          <span>info@tlane-studio.example</span>
        </li>
        <li class="contact__item">
          <svg class="contact__icon" viewBox="0 0 24 24" fill="none" stroke-width="2"><circle cx="12" cy="12" r="9"/><path d="M3 12h18M12 3c3 3 3 15 0 18M12 3c-3 3-3 15 0 18"/></svg>
          <span>www.tlane-studio.example</span>
        </li>
        <li class="contact__item">
          <span class="contact__marker"></span>
          <span>@t.lanestudio</span>
        </li>
      </ul>
    </div>

    <div class="accent-band"></div>
  </section>

</main>
</body>
</html>
```